Icons/images for company values

We have five company values, we have a new logo and a new look. I would like drawn images for each value that are in keeping with our look and feel.

Target Market(s)

internal/staff

Industry/Entity Type

media compliance

Requirements
Must have
• colours aligned with logo.

```html
<!DOCTYPE html>
<html lang="en">
<head>
<meta charset="utf-8">
<title>Company Values 2023</title>
<link href="https://fonts.googleapis.com/css2?family=Poppins:wght@300;400;500;700;800&display=swap" rel="stylesheet">
<style>
  :root {
    --page-bg: #ffffff;
    --panel-white: #f7f7f7;
    --navy: #3a6589;
    --blue: #4a84c8;
    --sky: #5b9dcb;
    --teal: #7cc8a6;
    --mint: #a6ee9c;
    --lime: #b9d86b;
    --yellow: #e7da52;
    --olive: #a3962c;
    --head-1: #35618a;
    --head-2: #4a8fbf;
    --head-3: #79c6a8;
    --head-4: #a6cf6a;
    --head-5: #a3962c;
    --ink: #1e1e1e;
    --white: #ffffff;
  }
  html, body {
    margin: 0;
    padding: 0;
    width: 707px;
    height: 1200px;
    overflow: hidden;
    background: var(--page-bg);
    font-family: "Poppins", sans-serif;
  }
  .values-poster {
    position: absolute;
    left: 20px;
    top: 342px;
    width: 667px;
    height: 516px;
    box-shadow: 0 6px 18px rgba(0,0,0,0.25);
  }
  .values-poster svg { display: block; width: 100%; height: 100%; }
  .brand-name { font-family: "Poppins", sans-serif; font-weight: 700; font-size: 38px; fill: var(--navy); }
  .hub-label { font-family: "Poppins", sans-serif; font-weight: 500; fill: var(--white); text-anchor: middle; }
  .value-number { font-family: "Poppins", sans-serif; font-weight: 700; font-size: 46px; fill: var(--navy); text-anchor: middle; }
  .value-title { font-family: "Poppins", sans-serif; font-weight: 800; font-size: 27px; }
  .value-body { font-family: "Poppins", sans-serif; font-weight: 400; font-size: 18.5px; fill: var(--ink); }
  .title-1 { fill: var(--head-1); }
  .title-2 { fill: var(--head-2); }
  .title-3 { fill: var(--head-3); }
  .title-4 { fill: var(--head-4); }
  .title-5 { fill: var(--head-5); }
  .icon { fill: none; stroke: var(--white); stroke-width: 4; stroke-linecap: round; stroke-linejoin: round; }
</style>
</head>
<body>
<div class="values-poster">
<svg viewBox="0 0 1237 957" xmlns="http://www.w3.org/2000/svg">
  <defs>
    <linearGradient id="field-gradient" x1="0" y1="0" x2="1" y2="1">
      <stop offset="0" stop-color="#3f6fb8"/>
      <stop offset="0.25" stop-color="#4a84c8"/>
      <stop offset="0.55" stop-color="#a6ee9c"/>
      <stop offset="1" stop-color="#e7da52"/>
    </linearGradient>
  </defs>

  <!-- backgrounds -->
  <rect class="field" x="279" y="0" width="958" height="957" fill="url(#field-gradient)"/>
  <rect class="side-panel" x="0" y="0" width="279" height="957" fill="var(--panel-white)"/>

  <!-- brand -->
  <text class="brand-name" x="44" y="215">Northvale</text>

  <!-- connector line -->
  <g class="connector" fill="none" stroke="var(--navy)" stroke-width="3">
    <circle cx="76" cy="313" r="7" fill="var(--white)"/>
    <polyline points="76,320 76,720 251,720"/>
    <circle cx="258" cy="720" r="7" fill="var(--white)"/>
  </g>

  <!-- value fan -->
  <g class="value-fan" stroke="var(--white)" stroke-width="7">
    <path d="M274 467 L274 122 A345 345 0 0 1 476.8 187.9 Z" fill="var(--navy)"/>
    <path d="M274 467 L476.8 187.9 A345 345 0 0 1 602.1 360.4 Z" fill="var(--sky)"/>
    <path d="M274 467 L602.1 360.4 A345 345 0 0 1 602.1 573.6 Z" fill="var(--teal)"/>
    <path d="M274 467 L602.1 573.6 A345 345 0 0 1 476.8 746.1 Z" fill="var(--lime)"/>
    <path d="M274 467 L476.8 746.1 A345 345 0 0 1 274 812 Z" fill="var(--yellow)"/>
  </g>

  <!-- small value icons -->
  <g class="icon">
    <path d="M351 238 C336 226 334 214 343 210 C348 208 351 212 351 215 C351 212 354 208 359 210 C368 214 366 226 351 238 Z" fill="var(--white)"/>
    <path d="M332 220 L332 240 L345 250 M370 220 L370 240 L357 250"/>
  </g>
  <g class="icon">
    <circle cx="476" cy="320" r="11"/>
    <path d="M458 308 A22 22 0 0 1 494 306 M494 306 L494 297 M494 332 A22 22 0 0 1 458 334 M458 334 L458 343"/>
  </g>
  <g class="icon">
    <circle cx="524" cy="460" r="14"/>
    <path d="M517 460 L522 465 L531 455 M516 481 L532 481 M518 488 L530 488"/>
    <path d="M500 460 L494 460 M548 460 L554 460 M507 442 L503 438 M541 442 L545 438 M524 436 L524 430"/>
  </g>
  <g class="icon">
    <circle cx="476" cy="608" r="13"/>
    <circle cx="476" cy="608" r="5"/>
    <path d="M464 622 L464 634 L490 634 L490 622"/>
  </g>
  <g class="icon">
    <path d="M338 690 L351 708 L364 690 M334 720 L345 702 M368 720 L357 702"/>
    <circle cx="351" cy="684" r="6" fill="var(--white)"/>
  </g>

  <!-- hub -->
  <circle cx="274" cy="467" r="184" fill="var(--white)" stroke="#c9d3dc" stroke-width="1.5"/>
  <circle cx="274" cy="467" r="156" fill="var(--navy)"/>
  <text class="hub-label" x="274" y="452" font-size="58">VALUES</text>
  <text class="hub-label" x="274" y="527" font-size="82">2023</text>

  <!-- value 01 -->
  <rect x="440" y="70" width="720" height="108" rx="54" fill="var(--white)"/>
  <circle cx="392" cy="137" r="62" fill="var(--white)" stroke="var(--navy)" stroke-width="6"/>
  <text class="value-number" x="392" y="154">01</text>
  <text class="value-title title-1" x="484" y="108">WE'RE OPEN AND HONEST</text>
  <text class="value-body" x="484" y="133">Sharing information helps us achieve the best outcomes for our teams</text>
  <text class="value-body" x="484" y="156">and business. We value open, honest, and clear communication.</text>

  <!-- value 02 -->
  <rect x="600" y="235" width="560" height="108" rx="54" fill="var(--white)"/>
  <circle cx="553" cy="283" r="62" fill="var(--white)" stroke="var(--navy)" stroke-width="6"/>
  <text class="value-number" x="553" y="300">02</text>
  <text class="value-title title-2" x="638" y="270">WE GET  THERE FASTER TOGETHER</text>
  <text class="value-body" x="638" y="297">Collaboration is at the heart of what we do, no</text>
  <text class="value-body" x="638" y="320">matter our team</text>

  <!-- value 03 -->
  <rect x="640" y="400" width="520" height="160" rx="60" fill="var(--white)"/>
  <circle cx="609" cy="478" r="62" fill="var(--white)" stroke="var(--navy)" stroke-width="6"/>
  <text class="value-number" x="609" y="495">03</text>
  <text class="value-title title-3" x="681" y="438">WE ARE LEADERS IN COPYRIGHT</text>
  <text class="value-title title-3" x="681" y="468">AND INTELLECTUAL PROPERTY</text>
  <text class="value-body" x="683" y="496">Leading the conversation in audio-visual</text>
  <text class="value-body" x="683" y="519">copyright compliance and advocating for</text>
  <text class="value-body" x="683" y="542">the protection of intellectual property globally.</text>

  <!-- value 04 -->
  <rect x="590" y="610" width="575" height="108" rx="54" fill="var(--white)"/>
  <circle cx="543" cy="668" r="62" fill="var(--white)" stroke="var(--navy)" stroke-width="6"/>
  <text class="value-number" x="543" y="685">04</text>
  <text class="value-title title-4" x="638" y="646">WE GET THINGS DONE</text>
  <text class="value-body" x="638" y="672">We grow through capability, focus and hard work. We</text>
  <text class="value-body" x="638" y="695">believe small steps compound to bigresults.</text>

  <!-- value 05 -->
  <rect x="410" y="760" width="750" height="108" rx="54" fill="var(--white)"/>
  <circle cx="363" cy="800" r="62" fill="var(--white)" stroke="var(--navy)" stroke-width="6"/>
  <text class="value-number" x="363" y="817">05</text>
  <text class="value-title title-5" x="453" y="800">DIVERSE PERSPECTIVES BUILD BETTER OUTCOMES</text>
  <text class="value-body" x="451" y="827">We value diversity, inclusion, respect and trust within our teams. We are</text>
  <text class="value-body" x="451" y="850">building a truly global organisation.</text>
</svg>
</div>
</body>
</html>
```